Restaurant Finder Website Design

I need to create a website that will help people find restaurants around a zip code or address.

I would like to have a very clean and simple design. I will need a design for the homepage, that should be very clean and simple to use. its where the users will launch their search. I am thinking something like tavuro like.. big search field with a very clean page where users can create an account or restaurants subscribe to the service.

Also need the design of the search results page, I would like to display a big map with the results and a list on the side or the bottom of the map.

Also need a profile page for the users that sign up to the site.

Mostly what I need are guidelines and color coordinated elements, like a general layout and buttons that work together. I would like to know what the action buttons and elements should look like. Because its going to have some more detail pages.

Target Market(s)

People in general, mainly people that work at an office and have to find a place for lunch every day.

Industry/Entity Type

Restaurant

Number of Pages Required

4 page

Font styles to use
Serif
Sans Serif

Requirements
Must have
• It must be a really simple and clean design but look edgy.

```html
<!DOCTYPE html>
<html lang="en">
<head>
<meta charset="utf-8">
<title>Dishnear — Find restaurants near you</title>
<link href="https://fonts.googleapis.com/css2?family=Hind:wght@400;500;600&display=swap" rel="stylesheet">
<style>
  :root{
    --brand-red:#c9202a;
    --ink:#33353d;
    --button-dark:#2f3139;
    --card:rgba(246,246,246,0.93);
    --white:#ffffff;
    --icon-grey:#8a8a8a;
    --wood-dark:#4a3426;
    --wood-mid:#8a6a4e;
    --wood-light:#c8ab86;
  }
  *{box-sizing:border-box;margin:0;padding:0}
  html,body{width:1200px;height:738px;overflow:hidden}
  body{font-family:"Hind",sans-serif;color:var(--ink);position:relative}
  .backdrop{
    position:absolute;inset:0;
    background:linear-gradient(120deg,var(--wood-dark) 0%,var(--wood-mid) 35%,var(--wood-light) 60%,var(--wood-mid) 85%,var(--wood-dark) 100%);
  }
  .page-card{
    position:absolute;left:125px;top:51px;width:952px;height:639px;
    background:var(--card);border-radius:11px;
  }
  .top-nav{
    position:absolute;right:23px;top:22px;display:flex;gap:12px;
    font-size:14px;color:var(--ink);
  }
  .top-nav a{color:inherit;text-decoration:none}
  .top-nav .sep{opacity:.8}
  .brand{
    position:absolute;left:0;right:0;top:112px;display:flex;justify-content:center;align-items:center;gap:18px;
  }
  .brand-dot{width:84px;height:84px;border-radius:50%;background:var(--brand-red)}
  .brand-name{font-size:46px;font-weight:500;color:var(--ink);letter-spacing:.5px}
  .search-panel{
    position:absolute;left:85px;top:260px;width:779px;height:257px;
    background:var(--brand-red);border-radius:7px;color:var(--white);
  }
  .panel-mark{position:absolute;left:383px;top:6px;width:13px;height:13px;border-radius:50%;background:var(--white)}
  .tagline{position:absolute;left:0;right:0;top:47px;text-align:center;font-size:20px;font-weight:400}
  .search-field{
    position:absolute;left:32px;top:96px;width:571px;height:48px;background:var(--white);border-radius:4px;
    display:flex;align-items:center;color:var(--ink);font-size:16px;
  }
  .field-part{display:flex;align-items:center;gap:12px;height:100%;padding-left:14px}
  .field-zip{width:271px;border-right:1px solid #d4d4d4;height:34px}
  .search-button{
    position:absolute;left:621px;top:95px;width:123px;height:47px;background:var(--button-dark);
    border-radius:4px;color:var(--white);font-size:18px;display:flex;align-items:center;justify-content:center;letter-spacing:.3px;
  }
  .divider{position:absolute;left:279px;top:165px;width:222px;height:12px;display:flex;align-items:center;gap:8px}
  .divider span{flex:1;height:1px;background:var(--white)}
  .divider i{width:12px;height:12px;border-radius:50%;background:var(--white)}
  .create-account{
    position:absolute;left:311px;top:196px;width:160px;height:42px;background:var(--button-dark);border-radius:4px;
    color:var(--white);font-size:15px;display:flex;align-items:center;justify-content:center;
  }
  .copyright{position:absolute;left:0;right:0;top:602px;text-align:center;font-size:14px;color:var(--ink)}
</style>
</head>
<body>
  <div class="backdrop" role="img" aria-label="Photo of a wooden restaurant table with shared plates, nachos and drinks"></div>

  <main class="page-card">
    <nav class="top-nav">
      <a href="#">Order Food</a><span class="sep">|</span>
      <a href="#">Book a Table</a><span class="sep">|</span>
      <a href="#">Login</a>
    </nav>

    <div class="brand">
      <span class="brand-dot"></span>
      <span class="brand-name">Dishnear</span>
    </div>

    <section class="search-panel">
      <span class="panel-mark"></span>
      <h1 class="tagline">We help peopel find restaurants arround a zip code or address</h1>

      <div class="search-field">
        <label class="field-part field-zip">
          <svg width="22" height="24" viewBox="0 0 22 24" aria-hidden="true">
            <path d="M11 1a6 6 0 0 0-6 6c0 4.5 6 10 6 10s6-5.5 6-10a6 6 0 0 0-6-6z" fill="var(--icon-grey)"/>
            <circle cx="11" cy="7" r="2.2" fill="#fff"/>
            <path d="M3 17l-2 6h20l-2-6" fill="none" stroke="var(--icon-grey)" stroke-width="1.4"/>
          </svg>
          Enter Zip Code
        </label>
        <label class="field-part">
          <svg width="20" height="18" viewBox="0 0 20 18" aria-hidden="true">
            <path d="M1 17V7l5 3V7l5 3V3h3v-2h2v2h3v14z" fill="var(--icon-grey)"/>
            <rect x="4" y="12" width="2" height="2" fill="#fff"/><rect x="8" y="12" width="2" height="2" fill="#fff"/><rect x="12" y="12" width="2" height="2" fill="#fff"/>
          </svg>
          Enter Address
        </label>
      </div>
      <a class="search-button">SEARCH</a>

      <div class="divider"><span></span><i></i><span></span></div>
      <a class="create-account">Create Account</a>
    </section>

    <footer class="copyright">© 2016 Copyright Dishnear All Rights Reserved.</footer>
  </main>
</body>
</html>
```